Aunt Roula's Bakery

I am about to create a luxury boutique that specializes in cake baking and cupcake
and ready for parties and special events and order delivery
the logo has already made

Boutique

Email:auntroulasbakery@mailbox-example.net
Instagram: aunt_roula_bakery
Twitter: xxxxxxx
WhatsApp: xxxxxxx

Requirements
Must have
• luxury design

```html
<!DOCTYPE html>
<html lang="en">
<head>
<meta charset="utf-8">
<title>Aunt Roula's Bakery – Business Card</title>
<link rel="stylesheet" href="https://fonts.googleapis.com/css2?family=Arimo:wght@400;700&display=swap">
<style>
  :root {
    --stage: #4a403c;
    --card: #131212;
    --card-edge: #1d1c1c;
    --pink: #f0a8c4;
    --mauve: #9e6a7a;
    --ring: #2c2a2a;
    --ring-line: #6a6666;
    --white: #f2f2f2;
    --grey: #a9a6a6;
  }
  * { box-sizing: border-box; margin: 0; padding: 0; }
  html, body {
    width: 1200px; height: 787px; overflow: hidden;
    background: var(--stage);
    font-family: "Arimo", Arial, sans-serif;
  }
  .stage {
    position: relative; width: 1200px; height: 787px;
    display: flex; align-items: center; justify-content: center; gap: 40px;
  }
  .card {
    position: relative; width: 540px; height: 310px;
    background: var(--card);
    border: 1px solid var(--card-edge);
    box-shadow: 0 10px 24px rgba(0,0,0,.45);
  }

  /* Front */
  .front__badge {
    position: absolute; left: 120px; top: 50px;
    width: 170px; height: 170px; border-radius: 50%;
    background: var(--ring);
    border: 2px solid var(--ring-line);
    display: flex; align-items: center; justify-content: center;
  }
  .front__disc {
    width: 146px; height: 146px; border-radius: 50%;
    background: var(--mauve);
    display: flex; align-items: center; justify-content: center;
    text-align: center; padding: 18px;
    color: var(--white); font-weight: 700; font-size: 17px;
    letter-spacing: 1px; line-height: 1.25; text-transform: uppercase;
  }
  .front__web {
    position: absolute; left: 96px; top: 238px;
    color: var(--white); font-size: 12px; letter-spacing: 3px;
  }

  /* Back */
  .back__brand {
    position: absolute; left: 200px; top: 34px; width: 290px;
    display: flex; align-items: center; justify-content: center; gap: 10px;
  }
  .back__brand-dot {
    width: 26px; height: 26px; border-radius: 50%; background: var(--mauve); flex: none;
  }
  .back__brand-name {
    color: var(--grey); font-size: 20px; font-weight: 400;
    letter-spacing: 2px; text-transform: uppercase;
  }
  .back__rule { position: absolute; left: 200px; width: 290px; height: 12px; }
  .back__rule--top { top: 84px; }
  .back__rule--bottom { top: 270px; left: 150px; width: 200px; }
  .back__person { position: absolute; left: 200px; top: 104px; width: 290px; text-align: center; }
  .back__name { color: var(--pink); font-size: 21px; font-weight: 700; }
  .back__role { color: var(--white); font-size: 15px; margin-top: 4px; }
  .back__contacts {
    position: absolute; left: 70px; top: 168px; width: 450px;
    list-style: none; display: flex; flex-wrap: wrap; row-gap: 10px; column-gap: 16px;
    color: var(--white); font-size: 14px;
  }
  .back__contacts li { display: flex; align-items: center; gap: 6px; }
  .icon { width: 14px; height: 14px; flex: none; }
  .bullet { width: 8px; height: 8px; border-radius: 50%; background: var(--pink); flex: none; }
</style>
</head>
<body>
<main class="stage">
  <section class="card card--front" aria-label="Card front">
    <div class="front__badge">
      <div class="front__disc">Aunt Roula's Bakery</div>
    </div>
    <p class="front__web">www.roulabakery.example</p>
  </section>

  <section class="card card--back" aria-label="Card back">
    <div class="back__brand">
      <span class="back__brand-dot"></span>
      <span class="back__brand-name">Aunt Roula's Bakery</span>
    </div>

    <svg class="back__rule back__rule--top" viewBox="0 0 290 12" aria-hidden="true">
      <line x1="8" y1="6" x2="282" y2="6" stroke="var(--pink)" stroke-width="1.5"/>
      <polygon points="0,6 9,2 9,10" fill="var(--pink)"/>
      <polygon points="290,6 281,2 281,10" fill="var(--pink)"/>
    </svg>

    <div class="back__person">
      <p class="back__name">Sami Khoury</p>
      <p class="back__role">President</p>
    </div>

    <ul class="back__contacts">
      <li>
        <svg class="icon" viewBox="0 0 16 16" aria-hidden="true"><path fill="var(--pink)" d="M3.6 1h2.6l1.2 3.2-1.7 1.2a8 8 0 0 0 4.9 4.9l1.2-1.7L15 9.8v2.6A1.6 1.6 0 0 1 13.4 14C7 14 2 9 2 2.6A1.6 1.6 0 0 1 3.6 1z"/></svg>
        555 0142 7788
      </li>
      <li>
        <svg class="icon" viewBox="0 0 16 16" aria-hidden="true"><rect x="1" y="3" width="14" height="10" fill="var(--pink)"/><path d="M1 3l7 6 7-6" fill="none" stroke="var(--card)" stroke-width="1.4"/></svg>
        auntroulasbakery@mailbox-example.net
      </li>
      <li><span class="bullet"></span>aunt_roula_bakery</li>
      <li><span class="bullet"></span>auntroulasbakery</li>
      <li><span class="bullet"></span>auntroulasbakery</li>
    </ul>

    <svg class="back__rule back__rule--bottom" viewBox="0 0 200 12" aria-hidden="true">
      <line x1="8" y1="6" x2="192" y2="6" stroke="var(--pink)" stroke-width="1.5"/>
      <polygon points="0,6 9,2 9,10" fill="var(--pink)"/>
      <polygon points="200,6 191,2 191,10" fill="var(--pink)"/>
    </svg>
  </section>
</main>
</body>
</html>
```